Playful Website Design Needed Pet Sitting and Dog Walking Business

Need a simple one page Web Design Built on WordPress.
Sections:

About Us
Services Provided
Costs
Contact Us
Intake Form (Questionnaire that goes to email)
See us in Action

Industry/Entity Type

Pet Sitting and Dog Walking

Number of Pages Required

1 page

Font styles to use
Other font styles liked:
• See the Business Card Font and use that.

Colors
EE7325
F08F49
F5BC92
FAE3D3
FDF4ED

Requirements
Must have
• See attached Logo Design, with Font's and Colors Use these as theme guide

```html
<!DOCTYPE html>
<html lang="en">
<head>
<meta charset="UTF-8">
<title>Paw Pal Sitters</title>
<link href="https://fonts.googleapis.com/css2?family=Mulish:wght@400;500;600;700;800&display=swap" rel="stylesheet">
<style>
:root{
  --green:#7bc143;
  --yellow:#ffe70a;
  --orange:#ee7325;
  --orange-soft:#f08f49;
  --peach:#f5bc92;
  --cream:#fae3d3;
  --ink:#222222;
  --text:#666666;
  --white:#ffffff;
}
*{margin:0;padding:0;box-sizing:border-box}
html,body{width:1200px;height:4188px;overflow:hidden;background:var(--white)}
body{font-family:"Mulish",sans-serif;color:var(--ink);position:relative}
.abs{position:absolute}
svg.bg{position:absolute;left:0;display:block}

/* header */
.brand{left:88px;top:-4px;width:188px;height:188px;border-radius:50%;background:var(--white);display:flex;align-items:center;justify-content:center;text-align:center;color:var(--orange);font-weight:800;font-size:24px;line-height:1.1;z-index:3}
.nav{left:458px;top:48px;display:flex;gap:38px;font-size:14px;font-weight:700;color:var(--white);z-index:3}
.nav a{color:inherit;text-decoration:none;position:relative}
.nav a.active::after{content:"";position:absolute;left:0;right:0;bottom:-8px;height:2px;background:var(--white)}
.quote-btn{left:934px;top:37px;width:154px;height:46px;border-radius:23px;background:var(--orange);color:var(--white);font-size:14px;font-weight:700;display:flex;align-items:center;justify-content:center;z-index:3}

/* hero */
.hero-title{left:152px;top:308px;font-size:72px;font-weight:800;line-height:1;color:#2a2a2a;z-index:2}
.hero-text{left:158px;top:472px;width:430px;font-size:13.5px;line-height:26px;font-weight:600;z-index:2}
.hero-btn{left:158px;top:546px;width:170px;height:47px;border-radius:24px;background:var(--orange);color:var(--white);font-size:14px;font-weight:700;display:flex;align-items:center;justify-content:center;z-index:2}
.hero-photo{left:560px;top:150px;width:610px;height:648px;background:linear-gradient(180deg,#f4d9c5,#c98a52 60%,#efe3dc);border-radius:300px 300px 0 0;z-index:1}
.arrow{width:56px;height:56px;border-radius:50%;background:#5d5a12;display:flex;align-items:center;justify-content:center;z-index:2}

/* about */
.about-blob{left:130px;top:906px;width:424px;height:436px;border-radius:54% 46% 52% 48% / 50% 55% 45% 50%;background:var(--orange)}
.about-photo{left:140px;top:906px;width:410px;height:434px;border-radius:48% 52% 50% 50% / 44% 50% 50% 56%;background:linear-gradient(150deg,#e8e2dc,#9b6a44 55%,#f1ede8)}
.h2{font-size:45px;font-weight:600;color:#2a2a2a}
.about-text{left:620px;top:964px;width:468px;font-size:13.5px;line-height:25.6px;color:var(--text);text-align:justify}
.about-text p+p{margin-top:25px}
.call-label{left:705px;top:1298px;font-size:13.5px;font-weight:700}
.call-num{left:705px;top:1322px;font-size:21px;font-weight:600;color:var(--orange)}

/* services */
.services-title{left:0;width:1200px;top:1578px;text-align:center;color:var(--white);font-size:42px;font-weight:600}
.ring{width:254px;height:254px;border-radius:50%;background:#d9651d;display:flex;align-items:center;justify-content:center}
.ring .ph{width:212px;height:212px;border-radius:50%}
.svc{width:280px;text-align:center;color:var(--white)}
.svc h3{font-size:21px;font-weight:600;margin-bottom:10px}
.svc p{font-size:13px;font-weight:700;line-height:26px}

/* costs */
.costs-title{left:0;width:1200px;top:2382px;text-align:center}
.card{width:242px;height:350px;background:var(--white);box-shadow:0 2px 12px rgba(0,0,0,.12);padding:22px 20px}
.card.featured{height:392px;background:linear-gradient(180deg,#f55d0a,#7bc143 70%);color:var(--white);padding-top:44px}
.card .tier{font-size:13px;font-weight:700}
.card .price{font-size:22px;font-weight:600;margin:10px 0 12px}
.card .price small{font-size:13px}
.card ul{list-style:none}
.card li{font-size:12.5px;line-height:34px;color:var(--text);display:flex;align-items:center;gap:10px}
.card.featured li{color:var(--white)}
.card li svg{flex:none}
.plan-btn{margin-top:14px;width:128px;height:47px;border:2px solid var(--green);border-radius:6px;color:var(--green);font-size:14px;font-weight:600;display:flex;align-items:center;justify-content:center}
.card.featured .plan-btn{border-color:var(--white);color:var(--white)}

/* contact */
.contact-title{left:0;width:1200px;top:3008px;text-align:center;color:var(--white)}
.info-icon{width:64px;height:64px;border-radius:50%;background:linear-gradient(135deg,#f37a3a,#f5bc92);display:flex;align-items:center;justify-content:center}
.info-text{color:var(--white);font-size:13px;font-weight:600;line-height:20px}
.info-text b{display:block;font-size:15px;font-weight:700;margin-bottom:4px}
.field{background:var(--white);border-radius:3px;font-size:14px;color:#666;padding:0 16px;display:flex;align-items:center}
.send-btn{left:514px;top:3374px;width:172px;height:52px;border-radius:26px;background:linear-gradient(180deg,#ee7325,#f5bc92);color:var(--white);font-size:15px;font-weight:600;display:flex;align-items:center;justify-content:center}

/* footer */
.f-head{font-size:18px;font-weight:600;letter-spacing:.5px}
.f-head::after{content:"";display:block;width:64px;height:3px;background:var(--green);margin-top:14px}
.f-text{font-size:12.5px;line-height:26px;color:#444}
.f-links{list-style:none;font-size:12.5px;line-height:26.6px;color:#444}
.f-links li::before{content:"›";margin-right:16px}
.email-box{left:111px;top:3798px;width:329px;height:50px;border:1px solid #bbb;border-radius:6px;font-size:13px;color:#444;padding:0 20px;display:flex;align-items:center}
.sub-btn{left:111px;top:3860px;width:131px;height:48px;border-radius:4px;background:var(--orange);color:var(--white);font-size:14px;font-weight:800;display:flex;align-items:center;justify-content:center}
.f-contact{font-size:12.5px;color:#444;line-height:26px;display:flex;gap:22px}
.rule{left:111px;top:3922px;width:977px;height:1px;background:#e5e5e5}
.copy{left:0;width:1200px;top:3954px;text-align:center;font-size:13px;color:#333}
.grass{left:0;top:4024px;width:1200px;height:164px;background:linear-gradient(180deg,#b6e07a,#6cb82d 45%,#3f8c15)}
</style>
</head>
<body>

<!-- top bands -->
<svg class="bg" style="top:0" width="1200" height="810" viewBox="0 0 1200 810" aria-hidden="true">
  <rect width="1200" height="260" fill="#7bc143"/>
  <path d="M0 120 C200 190 320 170 520 150 C760 125 900 120 1050 150 C1120 165 1170 160 1200 150 L1200 760 C1100 800 1000 800 860 770 C720 740 640 790 520 800 C380 810 300 740 180 760 C90 775 40 790 0 780 Z" fill="#ffe70a"/>
</svg>

<div class="abs brand">Paw Pal<br>Sitters</div>
<nav class="abs nav"><a class="active">Home</a><a>About Us</a><a>Services</a><a>Costs</a><a>Contact Us</a></nav>
<div class="abs quote-btn">Get a Quote</div>

<div class="abs hero-photo" role="img" aria-label="Smiling young woman holding two fluffy puppies"></div>
<h1 class="abs hero-title">Paw Pal<br>Sitters</h1>
<p class="abs hero-text">Lorem ipsum dolor sit amet, consectetur adipiscing elit, sed do eiusmod tempor incididunt ut labore et dolore</p>
<div class="abs hero-btn">GET STARTED&nbsp;›</div>
<div class="abs arrow" style="left:27px;top:423px"><svg width="16" height="16" viewBox="0 0 16 16"><path d="M10 2 L4 8 L10 14" stroke="#fff" stroke-width="2.5" fill="none"/></svg></div>
<div class="abs arrow" style="left:1117px;top:423px"><svg width="16" height="16" viewBox="0 0 16 16"><path d="M6 2 L12 8 L6 14" stroke="#fff" stroke-width="2.5" fill="none"/></svg></div>

<!-- about -->
<div class="abs about-blob"></div>
<div class="abs about-photo" role="img" aria-label="Person spoon-feeding a boxer puppy wearing a bib"></div>
<h2 class="abs h2" style="left:620px;top:888px">About Us</h2>
<div class="abs about-text">
  <p>Lorem ipsum dolor sit amet, consectetur adipiscing elit, sed do eiusmod tempor incididunt ut labore et dolore magna aliqua. Ut enim ad minim veniam, quis nostrud exercitation ullamco laboris nisi ut aliquip ex ea commodo consequat. Duis aute irure dolor in reprehenderit in voluptate velit esse cillum dolore</p>
  <p>Eu fugiat nulla pariatur. Excepteur sint occaecat cupidatat non proident, sunt in culpa qui officia deserunt mollit anim id est laborum. Lorem ipsum dolor sit amet, consectetur adipiscing elit, sed do eiusmod tempor incididunt ut labore et dolore magna aliqua. Ut enim ad minim veniam, quis nostrud exercitation ullamco laboris nisi ut aliquip ex ea commodo consequat.</p>
</div>
<svg class="abs" style="left:624px;top:1292px" width="56" height="56" viewBox="0 0 56 56" aria-hidden="true">
  <path d="M10 10 C6 14 6 22 12 32 C18 42 28 50 36 50 C40 50 44 46 44 42 L36 36 L30 40 C24 36 20 32 16 26 L20 20 L14 10 Z" fill="none" stroke="#ee7325" stroke-width="2.5" stroke-linejoin="round"/>
  <path d="M30 14 A10 10 0 0 1 40 24 M30 7 A17 17 0 0 1 47 24 M30 0 A24 24 0 0 1 54 24" fill="none" stroke="#ee7325" stroke-width="2.5"/>
</svg>
<div class="abs call-label">Call us Today :</div>
<div class="abs call-num">+1 888 888 8888</div>

<!-- services -->
<svg class="bg" style="top:1430px" width="1200" height="870" viewBox="0 0 1200 870" aria-hidden="true">
  <path d="M0 30 C120 0 220 30 380 40 C560 52 700 60 860 40 C1000 22 1100 0 1200 30 L1200 820 C1080 790 980 850 800 846 C640 842 560 790 400 800 C240 810 120 850 0 840 Z" fill="#ee7325"/>
</svg>
<h2 class="abs services-title">Our Services</h2>

<div class="abs ring" style="left:146px;top:1658px"><div class="ph" role="img" aria-label="Woman hugging a shaggy dog" style="background:linear-gradient(135deg,#6b7a3c,#d8b27c)"></div></div>
<div class="abs ring" style="left:473px;top:1718px"><div class="ph" role="img" aria-label="Two dogs being bathed" style="background:linear-gradient(135deg,#4c3a2e,#c9b49a)"></div></div>
<div class="abs ring" style="left:798px;top:1658px"><div class="ph" role="img" aria-label="Woman training a small dog in a kitchen" style="background:linear-gradient(135deg,#f1efea,#e0a36a)"></div></div>

<div class="abs svc" style="left:133px;top:1926px"><h3>8$ per visit. 2 visits a day.</h3><p>Lorem ipsum dolor sit amet, cons ectetur adipiscing elit, sed do eius mod tempor incididunt ut labore et dolore magna aliqua.</p></div>
<div class="abs svc" style="left:460px;top:1986px"><h3>All pets, Any Age!</h3><p>Lorem ipsum dolor sit amet, cons ectetur adipiscing elit, sed do eius mod tempor incididunt ut labore et dolore magna aliqua.</p></div>
<div class="abs svc" style="left:785px;top:1926px"><h3>Parent Supervised.</h3><p>Lorem ipsum dolor sit amet, cons ectetur adipiscing elit, sed do eius mod tempor incididunt ut labore et dolore magna aliqua.</p></div>

<!-- costs -->
<h2 class="abs h2 costs-title">Our Costs</h2>

<div class="abs card" style="left:111px;top:2483px">
  <div class="tier">Intro</div><div class="price">$19<small>/monthly</small></div>
  <ul>
    <li><svg width="14" height="14" viewBox="0 0 14 14"><circle cx="7" cy="7" r="6" fill="none" stroke="#7bc143" stroke-width="1.5"/><path d="M4 7 L6.3 9.2 L10 5" stroke="#7bc143" stroke-width="1.5" fill="none"/></svg>Lorem ipsum dolor sit am</li>
    <li><svg width="14" height="14" viewBox="0 0 14 14"><circle cx="7" cy="7" r="6" fill="none" stroke="#7bc143" stroke-width="1.5"/><path d="M4 7 L6.3 9.2 L10 5" stroke="#7bc143" stroke-width="1.5" fill="none"/></svg>Et, consectetur adipiscing</li>
    <li><svg width="14" height="14" viewBox="0 0 14 14"><circle cx="7" cy="7" r="6" fill="none" stroke="#7bc143" stroke-width="1.5"/><path d="M4 7 L6.3 9.2 L10 5" stroke="#7bc143" stroke-width="1.5" fill="none"/></svg>Elit, sed do eiusmod temp</li>
    <li><svg width="14" height="14" viewBox="0 0 14 14"><circle cx="7" cy="7" r="6" fill="none" stroke="#7bc143" stroke-width="1.5"/><path d="M4 7 L6.3 9.2 L10 5" stroke="#7bc143" stroke-width="1.5" fill="none"/></svg>Or incididunt ut labore et</li>
    <li><svg width="14" height="14" viewBox="0 0 14 14"><circle cx="7" cy="7" r="6" fill="none" stroke="#7bc143" stroke-width="1.5"/><path d="M4 7 L6.3 9.2 L10 5" stroke="#7bc143" stroke-width="1.5" fill="none"/></svg>Dolore magna aliqua</li>
  </ul>
  <div class="plan-btn">Choose Plan</div>
</div>

<div class="abs card featured" style="left:356px;top:2465px">
  <div class="tier">Intro</div><div class="price">$19<small>/monthly</small></div>
  <ul>
    <li><svg width="14" height="14" viewBox="0 0 14 14"><circle cx="7" cy="7" r="6" fill="none" stroke="#fff" stroke-width="1.5"/><path d="M4 7 L6.3 9.2 L10 5" stroke="#fff" stroke-width="1.5" fill="none"/></svg>Lorem ipsum dolor sit am</li>
    <li><svg width="14" height="14" viewBox="0 0 14 14"><circle cx="7" cy="7" r="6" fill="none" stroke="#fff" stroke-width="1.5"/><path d="M4 7 L6.3 9.2 L10 5" stroke="#fff" stroke-width="1.5" fill="none"/></svg>Et, consectetur adipiscing</li>
    <li><svg width="14" height="14" viewBox="0 0 14 14"><circle cx="7" cy="7" r="6" fill="none" stroke="#fff" stroke-width="1.5"/><path d="M4 7 L6.3 9.2 L10 5" stroke="#fff" stroke-width="1.5" fill="none"/></svg>Elit, sed do eiusmod temp</li>
    <li><svg width="14" height="14" viewBox="0 0 14 14"><circle cx="7" cy="7" r="6" fill="none" stroke="#fff" stroke-width="1.5"/><path d="M4 7 L6.3 9.2 L10 5" stroke="#fff" stroke-width="1.5" fill="none"/></svg>Or incididunt ut labore et</li>
    <li><svg width="14" height="14" viewBox="0 0 14 14"><circle cx="7" cy="7" r="6" fill="none" stroke="#fff" stroke-width="1.5"/><path d="M4 7 L6.3 9.2 L10 5" stroke="#fff" stroke-width="1.5" fill="none"/></svg>Dolore magna aliqua</li>
  </ul>
  <div class="plan-btn">Choose Plan</div>
</div>

<div class="abs card" style="left:602px;top:2483px">
  <div class="tier">Intro</div><div class="price">$19<small>/monthly</small></div>
  <ul>
    <li><svg width="14" height="14" viewBox="0 0 14 14"><circle cx="7" cy="7" r="6" fill="none" stroke="#7bc143" stroke-width="1.5"/><path d="M4 7 L6.3 9.2 L10 5" stroke="#7bc143" stroke-width="1.5" fill="none"/></svg>Lorem ipsum dolor sit am</li>
    <li><svg width="14" height="14" viewBox="0 0 14 14"><circle cx="7" cy="7" r="6" fill="none" stroke="#7bc143" stroke-width="1.5"/><path d="M4 7 L6.3 9.2 L10 5" stroke="#7bc143" stroke-width="1.5" fill="none"/></svg>Et, consectetur adipiscing</li>
    <li><svg width="14" height="14" viewBox="0 0 14 14"><circle cx="7" cy="7" r="6" fill="none" stroke="#7bc143" stroke-width="1.5"/><path d="M4 7 L6.3 9.2 L10 5" stroke="#7bc143" stroke-width="1.5" fill="none"/></svg>Elit, sed do eiusmod temp</li>
    <li><svg width="14" height="14" viewBox="0 0 14 14"><circle cx="7" cy="7" r="6" fill="none" stroke="#7bc143" stroke-width="1.5"/><path d="M4 7 L6.3 9.2 L10 5" stroke="#7bc143" stroke-width="1.5" fill="none"/></svg>Or incididunt ut labore et</li>
    <li><svg width="14" height="14" viewBox="0 0 14 14"><circle cx="7" cy="7" r="6" fill="none" stroke="#7bc143" stroke-width="1.5"/><path d="M4 7 L6.3 9.2 L10 5" stroke="#7bc143" stroke-width="1.5" fill="none"/></svg>Dolore magna aliqua</li>
  </ul>
  <div class="plan-btn">Choose Plan</div>
</div>

<div class="abs card" style="left:847px;top:2483px">
  <div class="tier">Intro</div><div class="price">$19<small>/monthly</small></div>
  <ul>
    <li><svg width="14" height="14" viewBox="0 0 14 14"><circle cx="7" cy="7" r="6" fill="none" stroke="#7bc143" stroke-width="1.5"/><path d="M4 7 L6.3 9.2 L10 5" stroke="#7bc143" stroke-width="1.5" fill="none"/></svg>Lorem ipsum dolor sit am</li>
    <li><svg width="14" height="14" viewBox="0 0 14 14"><circle cx="7" cy="7" r="6" fill="none" stroke="#7bc143" stroke-width="1.5"/><path d="M4 7 L6.3 9.2 L10 5" stroke="#7bc143" stroke-width="1.5" fill="none"/></svg>Et, consectetur adipiscing</li>
    <li><svg width="14" height="14" viewBox="0 0 14 14"><circle cx="7" cy="7" r="6" fill="none" stroke="#7bc143" stroke-width="1.5"/><path d="M4 7 L6.3 9.2 L10 5" stroke="#7bc143" stroke-width="1.5" fill="none"/></svg>Elit, sed do eiusmod temp</li>
    <li><svg width="14" height="14" viewBox="0 0 14 14"><circle cx="7" cy="7" r="6" fill="none" stroke="#7bc143" stroke-width="1.5"/><path d="M4 7 L6.3 9.2 L10 5" stroke="#7bc143" stroke-width="1.5" fill="none"/></svg>Or incididunt ut labore et</li>
    <li><svg width="14" height="14" viewBox="0 0 14 14"><circle cx="7" cy="7" r="6" fill="none" stroke="#7bc143" stroke-width="1.5"/><path d="M4 7 L6.3 9.2 L10 5" stroke="#7bc143" stroke-width="1.5" fill="none"/></svg>Dolore magna aliqua</li>
  </ul>
  <div class="plan-btn">Choose Plan</div>
</div>

<!-- contact -->
<svg class="bg" style="top:2959px" width="1200" height="600" viewBox="0 0 1200 600" aria-hidden="true">
  <path d="M101 0 H1101 V550 C1020 520 960 510 860 545 C760 580 700 540 600 540 C480 540 420 580 320 560 C220 540 160 520 101 555 Z" fill="#7bc143"/>
</svg>
<h2 class="abs h2 contact-title">Contact Us</h2>

<div class="abs info-icon" style="left:211px;top:3106px"><svg width="26" height="26" viewBox="0 0 26 26"><path d="M13 2 C8 2 5 6 5 10 C5 16 13 24 13 24 C13 24 21 16 21 10 C21 6 18 2 13 2 Z" fill="none" stroke="#fff" stroke-width="2"/><circle cx="13" cy="10" r="3" fill="#fff"/></svg></div>
<div class="abs info-text" style="left:298px;top:3104px"><b>LOCATION:</b>465, Lorum Ipsum Dolore,<br>United States</div>
<div class="abs info-icon" style="left:517px;top:3106px"><svg width="26" height="26" viewBox="0 0 26 26"><path d="M5 4 C3 6 3 10 6 15 C9 20 14 23 18 23 C20 23 22 21 22 19 L18 16 L15 18 C12 16 10 14 8 11 L10 8 L7 4 Z" fill="#fff"/><path d="M15 5 A6 6 0 0 1 21 11 M15 1 A10 10 0 0 1 25 11" fill="none" stroke="#fff" stroke-width="1.8"/></svg></div>
<div class="abs info-text" style="left:604px;top:3114px"><b>CALL US:</b>+1 (888) 888 8888</div>
<div class="abs info-icon" style="left:765px;top:3106px"><svg width="26" height="26" viewBox="0 0 26 26"><rect x="3" y="6" width="20" height="14" rx="2" fill="none" stroke="#fff" stroke-width="2"/><path d="M3 7 L13 14 L23 7" fill="none" stroke="#fff" stroke-width="2"/></svg></div>
<div class="abs info-text" style="left:853px;top:3114px"><b>EMAIL US:</b>hello@pawpalsitters.com</div>

<div class="abs field" style="left:166px;top:3203px;width:282px;height:49px">Full Name</div>
<div class="abs field" style="left:459px;top:3203px;width:282px;height:49px">Phone</div>
<div class="abs field" style="left:751px;top:3203px;width:283px;height:49px">Email Address</div>
<div class="abs field" style="left:166px;top:3263px;width:868px;height:95px;align-items:flex-start;padding-top:14px">Message</div>
<div class="abs send-btn">SEND MESSAGE</div>

<!-- footer -->
<h3 class="abs f-head" style="left:111px;top:3668px">SUBSCRIBE OUR NEWSLETTER</h3>
<p class="abs f-text" style="left:111px;top:3728px;width:305px;text-align:justify">Lorem ipsum dolor sit amet, consectetur adipiscing elit, sed do</p>
<div class="abs email-box">Email address</div>
<div class="abs sub-btn">SUBSCRIBE</div>

<h3 class="abs f-head" style="left:538px;top:3668px">QUICK LINKS</h3>
<ul class="abs f-links" style="left:538px;top:3728px">
  <li>Home</li><li>About us</li><li>Project</li><li>Services</li><li>Portfolio</li><li>Contact us</li>
</ul>

<h3 class="abs f-head" style="left:885px;top:3668px">CONTACT US</h3>
<div class="abs f-contact" style="left:887px;top:3728px"><svg width="10" height="14" viewBox="0 0 10 14" style="margin-top:6px"><path d="M5 0 C2 0 0 2 0 5 C0 9 5 14 5 14 C5 14 10 9 10 5 C10 2 8 0 5 0 Z" fill="#333"/><circle cx="5" cy="5" r="2" fill="#fff"/></svg><span>123,Lorem ipsum dolor sit<br>amet, consectetur</span></div>
<div class="abs f-contact" style="left:885px;top:3808px"><svg width="12" height="12" viewBox="0 0 12 12" style="margin-top:7px"><path d="M1 1 C0 3 1 6 4 9 C7 12 9 12 11 11 L11 8.5 L8.5 7.5 L7.5 8.5 C6 8 4 6 3.5 4.5 L4.5 3.5 L3.5 1 Z" fill="#333"/></svg><span>+1 888 888 8888</span></div>
<div class="abs f-contact" style="left:885px;top:3861px"><svg width="14" height="11" viewBox="0 0 14 11" style="margin-top:8px"><rect width="14" height="11" rx="1" fill="#333"/><path d="M0 1 L7 6 L14 1" stroke="#fff" stroke-width="1.2" fill="none"/></svg><span>info@pawpalsitters.com</span></div>

<div class="abs rule"></div>
<p class="abs copy">© Copyrights 2022 Paw Pal Sitters | All Rights reserved</p>

<div class="abs grass" role="img" aria-label="Strip of green grass along the bottom edge"></div>

</body>
</html>
```